FunBrixo Business Card

We need a business card design for our company. We sell construction-themed amusement rides for kids.

Contact Information for Business Card

Contact info on business card should include:
Carl Dunning
Co-Founder & COO
(833) 571-FUNBRIX
Carl@funbrixo-demo.com
www.funbrixo-demo.com

```html
<!DOCTYPE html>
<html lang="en">
<head>
<meta charset="utf-8">
<title>FunBrixo Business Card</title>
<link href="https://fonts.googleapis.com/css2?family=Lato:wght@400;700;900&display=swap" rel="stylesheet">
<style>
  :root {
    --stage: #3a3b3e;
    --ink: #0a0a0b;
    --paper: #ffffff;
    --orange: #f07b22;
    --purple: #8e2a8f;
    --grey: #4a4a4a;
  }
  * { box-sizing: border-box; margin: 0; padding: 0; }
  html, body { width: 1200px; height: 900px; overflow: hidden; }
  body {
    background: var(--stage);
    font-family: "Lato", sans-serif;
    display: flex;
    flex-direction: column;
    align-items: center;
    justify-content: center;
    gap: 36px;
  }
  .card {
    position: relative;
    width: 700px;
    height: 400px;
    border-radius: 28px;
    overflow: hidden;
    box-shadow: 0 18px 40px rgba(0,0,0,.45);
  }
  .card--back {
    background: var(--ink);
    display: flex;
    align-items: center;
    justify-content: center;
  }
  .brand-name {
    font-weight: 900;
    color: var(--orange);
    letter-spacing: .5px;
    line-height: 1;
  }
  .card--back .brand-name { font-size: 84px; }
  .card--front { background: var(--paper); }
  .front-shape { position: absolute; inset: 0; }
  .front-brand {
    position: absolute;
    right: 56px;
    top: 70px;
    font-size: 54px;
  }
  .holder {
    position: absolute;
    left: 48px;
    top: 150px;
  }
  .holder__name {
    font-weight: 700;
    font-size: 34px;
    text-transform: uppercase;
    letter-spacing: .5px;
  }
  .holder__first { color: var(--orange); }
  .holder__last { color: var(--purple); }
  .holder__role {
    margin-top: 6px;
    font-size: 20px;
    color: var(--grey);
  }
  .contacts {
    position: absolute;
    left: 236px;
    top: 292px;
    list-style: none;
    display: flex;
    flex-direction: column;
    gap: 8px;
  }
  .contacts li {
    display: flex;
    align-items: center;
    gap: 14px;
    color: var(--paper);
    font-size: 19px;
    line-height: 24px;
  }
  .contacts svg { width: 20px; height: 20px; flex: none; }
</style>
</head>
<body>
  <section class="card card--back" aria-label="Card back">
    <span class="brand-name">FunBrixo</span>
  </section>

  <section class="card card--front" aria-label="Card front">
    <svg class="front-shape" viewBox="0 0 700 400" aria-hidden="true">
      <path d="M110 400 C150 300 230 245 400 235 C540 228 600 160 700 70 L700 400 Z" fill="var(--ink)"/>
      <path d="M92 394 C138 286 230 226 470 217" fill="none" stroke="var(--orange)" stroke-width="7" stroke-linecap="round"/>
    </svg>

    <span class="brand-name front-brand">FunBrixo</span>

    <div class="holder">
      <p class="holder__name"><span class="holder__first">Carl</span> <span class="holder__last">Dunning</span></p>
      <p class="holder__role">Co-Founder &amp; COO</p>
    </div>

    <ul class="contacts">
      <li>
        <svg viewBox="0 0 24 24" aria-hidden="true"><path d="M6.6 10.8a15.1 15.1 0 0 0 6.6 6.6l2.2-2.2a1 1 0 0 1 1-.25 11.4 11.4 0 0 0 3.6.57 1 1 0 0 1 1 1V20a1 1 0 0 1-1 1A17 17 0 0 1 3 4a1 1 0 0 1 1-1h3.5a1 1 0 0 1 1 1c0 1.25.2 2.45.57 3.57a1 1 0 0 1-.25 1z" fill="var(--orange)"/></svg>
        (833) 571-FUNBRIX
      </li>
      <li>
        <svg viewBox="0 0 24 24" aria-hidden="true"><rect x="2" y="5" width="20" height="14" rx="1" fill="var(--orange)"/><path d="M2.5 6l9.5 7 9.5-7" fill="none" stroke="var(--ink)" stroke-width="1.6"/></svg>
        Carl@funbrixo-demo.com
      </li>
      <li>
        <svg viewBox="0 0 24 24" aria-hidden="true"><circle cx="12" cy="12" r="10" fill="var(--orange)"/><g fill="none" stroke="var(--ink)" stroke-width="1.3"><circle cx="12" cy="12" r="6.5"/><ellipse cx="12" cy="12" rx="3" ry="6.5"/><path d="M5.5 12h13M6.5 9h11M6.5 15h11"/></g></svg>
        www.funbrixo-demo.com
      </li>
    </ul>
  </section>
</body>
</html>
```